Thornbury Building Company - Card Design

I am looking to use the logo designs that you already did for me to develop a business card. I would like the card to have a black background and be double sided. I want white and green logo and text. I have attached an inspiration photo of a look that I like. I would like to use the Vertical Logo attached to take up the full front side of the card. On the back where I have my name and information, I would like to have the horizontal logo or maybe even just the image of the 'A' and trees without the text. I am open, but I am looking for something clean and simple and I want the green to really pop! Additional files can be found under Design #: 58302946

Target Market(s)

Homeowners

Industry/Entity Type

Construction

Contact Information for Business Card

Name: Marcus Thornbury, Title: Project Manager, Phone: 555.274.8136, Email: thornburybuildingcompany@mailvesta.com, address: 487 Larkspur Ln, Ashvale, CA 95033, Lic# 2468317

Colors
00AB8E
00BBA5
67D7C9
C6EFE9
E9F9F6

Requirements
Nice to have
• I would like to see the logos that I have already got from ArtLoomHub, though I am open to new ones

```html
<!DOCTYPE html>
<html lang="en">
<head>
<meta charset="utf-8">
<title>Thornbury Building Company – Business Card</title>
<link rel="stylesheet" href="https://fonts.googleapis.com/css2?family=Roboto:wght@400;700&display=swap">
<style>
  :root {
    --backdrop: #2a2a2a;
    --card: #1c1c1c;
    --green: #5cb946;
    --white: #ffffff;
  }
  * { margin: 0; padding: 0; box-sizing: border-box; }
  html, body { width: 1200px; height: 1059px; overflow: hidden; }
  body {
    position: relative;
    background: var(--backdrop);
    font-family: "Roboto", Arial, sans-serif;
    color: var(--white);
  }
  .card {
    position: absolute;
    background: var(--card);
    border-radius: 18px;
    overflow: hidden;
  }
  .card--front { left: 257px; top: 89px; width: 687px; height: 390px; }
  .card--back  { left: 254px; top: 547px; width: 693px; height: 393px; }

  .brand {
    position: absolute;
    display: flex;
    align-items: center;
    gap: 14px;
  }
  .brand__mark {
    flex: none;
    background: var(--green);
  }
  .brand__name {
    font-weight: 700;
    color: var(--white);
    text-transform: uppercase;
    line-height: 1.05;
    letter-spacing: 0.04em;
    white-space: nowrap;
  }
  .card--front .brand { left: 50%; top: 50%; transform: translate(-50%, -50%); }
  .card--front .brand__mark { width: 64px; height: 64px; }
  .card--front .brand__name { font-size: 32px; }

  .card--back .brand { left: 35px; top: 58px; }
  .card--back .brand__mark { width: 44px; height: 44px; }
  .card--back .brand__name { font-size: 22px; }

  .accent-bar {
    position: absolute; left: 0; top: 167px;
    width: 17px; height: 39px; background: var(--green);
  }
  .line { position: absolute; left: 35px; white-space: nowrap; }
  .person__name { top: 160px; font-size: 25px; font-weight: 700; color: var(--green); }
  .person__title { top: 192px; font-size: 15.5px; }
  .licence { top: 233px; font-size: 15px; color: var(--green); }
  .address { top: 256px; font-size: 15px; }
  .contact { display: flex; align-items: center; gap: 8px; font-size: 15px; }
  .contact--phone { top: 298px; }
  .contact--email { top: 326px; }
  .contact svg { width: 12px; height: 12px; fill: var(--green); flex: none; }
</style>
</head>
<body>
  <section class="card card--front" aria-label="Card front">
    <div class="brand">
      <span class="brand__mark" aria-hidden="true"></span>
      <span class="brand__name">Thornbury<br>Building Company</span>
    </div>
  </section>

  <section class="card card--back" aria-label="Card back">
    <div class="brand">
      <span class="brand__mark" aria-hidden="true"></span>
      <span class="brand__name">Thornbury<br>Building Company</span>
    </div>

    <span class="accent-bar" aria-hidden="true"></span>
    <p class="line person__name">MARCUS THORNBURY</p>
    <p class="line person__title">Project Manager</p>
    <p class="line licence">Lic# 2468317</p>
    <p class="line address">487 Larkspur Ln, Ashvale, CA 95033</p>
    <p class="line contact contact--phone">
      <svg viewBox="0 0 24 24" aria-hidden="true"><path d="M6.6 10.8a15.1 15.1 0 0 0 6.6 6.6l2.2-2.2c.3-.3.7-.4 1-.2 1.1.4 2.3.6 3.6.6.6 0 1 .4 1 1V20c0 .6-.4 1-1 1A17 17 0 0 1 3 4c0-.6.4-1 1-1h3.5c.6 0 1 .4 1 1 0 1.3.2 2.5.6 3.6.1.3 0 .7-.2 1z"/></svg>
      555.274.8136
    </p>
    <p class="line contact contact--email">
      <svg viewBox="0 0 24 24" aria-hidden="true"><path d="M2 5h20v14H2zM3.5 6.5 12 13l8.5-6.5z" fill-rule="evenodd"/></svg>
      thornburybuildingcompany@mailvesta.com
    </p>
  </section>
</body>
</html>
```